Lifecoach needs website design based on a standard Wordpress theme

I need a website for my new lifecoaching business that can be easily implemented in Wordpress, it needs to be compatible with a standard Wordpress theme. So I can place the pictures, texts etc. in a standard theme of Wordpress.

I want the design to be a very good feeling and playfull one, based on my logo.

Target Market(s)

I will coach people to reach their goals and dreams in life.

Industry/Entity Type

Business

Requirements
Must have
• Can be easy implemented in Wordpress.
Nice to have
• Photo's of nature are nice.

```html
<!DOCTYPE html>
<html lang="en">
<head>
<meta charset="utf-8">
<title>Sam Verhoeven Lifecoach</title>
<link href="https://fonts.googleapis.com/css2?family=Open+Sans:wght@400;600;700&display=swap" rel="stylesheet">
<style>
:root{
  --brand:#14b3ea;
  --navy:#0f4f7c;
  --deep:#0a4a73;
  --ink:#333;
  --muted:#666;
  --grey-bg:#f1f1f1;
  --white:#fff;
}
*{margin:0;padding:0;box-sizing:border-box}
html,body{width:690px;height:1200px;overflow:hidden}
body{font-family:"Open Sans",Arial,sans-serif;background:var(--white);color:var(--ink);position:relative}
.abs{position:absolute}
.hero{left:0;top:0;width:690px;height:394px;
  background:linear-gradient(180deg,#a9cdea 0%,#dbe7ee 22%,#e9a36c 38%,#e2762f 60%,#c9561c 100%)}
.brand{left:75px;top:18px;display:flex;align-items:center;gap:6px}
.brand-mark{width:37px;height:37px;border-radius:50%;border:3px solid var(--deep)}
.brand-name{font-size:12.5px;font-weight:600;color:var(--deep);line-height:1.1}
.brand-sub{display:block;font-size:7.5px;padding-left:18px}
.nav{left:269px;top:29px;width:346px;display:flex;justify-content:space-between;font-size:9.6px;color:#555}
.nav .active{color:var(--brand)}
.social-rail{left:669px;top:88px;display:flex;flex-direction:column;gap:6px}
.social-rail span{width:13px;height:13px;border-radius:50%;background:var(--white);border:2px solid #f3a75e}
.dots{left:304px;top:358px;width:82px;height:20px;border-radius:10px;background:var(--brand);display:flex;justify-content:center;align-items:center;gap:5px}
.dots span{width:5.5px;height:5.5px;border-radius:50%;background:var(--white)}
.dots span:first-child{background:var(--navy)}
.band{left:0;top:394px;width:690px;height:41px;background:var(--brand)}
.band-text{left:76px;top:407px;font-size:9.8px;letter-spacing:-0.15px;white-space:nowrap;color:var(--white)}
.band-btn{left:553px;top:406px;width:61px;height:16px;border-radius:8px;background:var(--navy);color:var(--white);font-size:7.5px;text-align:center;line-height:16px}
.welcome-title{left:0;width:690px;top:453px;text-align:center;font-size:13.5px;font-weight:700;color:var(--navy)}
.welcome-text{left:76px;top:479px;width:538px;text-align:center;font-size:7.3px;line-height:14px;color:var(--muted)}
.card{top:572px;width:167px}
.card-photo{width:167px;height:93px}
.card h3{margin-top:10px;font-size:10.3px;font-weight:600;color:var(--navy)}
.card p{margin-top:4px;font-size:6.6px;line-height:12.4px;color:var(--muted)}
.pill{display:inline-block;margin-top:5px;width:60px;height:17px;border-radius:9px;background:var(--brand);color:var(--white);font-size:7.3px;text-align:center;line-height:17px}
.testimonials{left:0;top:797px;width:690px;height:185px;background:var(--grey-bg)}
.testi-title{left:0;width:690px;top:818px;text-align:center;font-size:13.5px;font-weight:700;color:var(--navy)}
.testi-rule{left:75px;top:847px;width:539px;height:1px;background:#d8d8d8}
.quote{top:864px;width:152px}
.quote-mark{position:absolute;left:0;top:0;font-size:26px;font-weight:700;color:var(--brand);line-height:20px}
.quote p{font-size:6.6px;line-height:12.4px;color:var(--muted);text-indent:28px}
.quote .who{margin-top:5px;font-size:7.5px;color:var(--brand)}
.footer{left:0;top:982px;width:690px;height:218px;background:var(--deep)}
.foot-h{top:1003px;font-size:12px;font-weight:400;color:var(--white)}
.foot-links{top:1033px;font-size:7.6px;line-height:16.3px;color:#e6eef4;list-style:none}
.tweet{left:302px;top:1035px;width:138px;font-size:7.3px;line-height:13.5px;color:#e6eef4}
.tweet .date{margin-top:4px}
.tweet-btn{left:302px;top:1107px;width:97px;height:17px;border-radius:3px;background:#06395b;color:var(--white);font-size:7.8px;text-align:center;line-height:17px}
.mail{left:475px;top:1038px;width:139px;height:22px;border-radius:3px;background:var(--white);font-size:7.8px;color:#999;padding-left:10px;line-height:22px}
.submit{left:475px;top:1069px;width:63px;height:19px;border-radius:10px;background:var(--brand);color:var(--white);font-size:9px;font-weight:700;text-align:center;line-height:19px}
.follow{left:475px;top:1112px;font-size:10.5px;color:var(--white);display:flex;align-items:center;gap:8px}
.follow span{width:9px;height:9px;border-radius:50%;background:var(--white)}
.follow span:first-child{margin-left:4px}
.foot-rule{left:75px;top:1152px;width:539px;height:1px;background:#1e5d86}
.legal{left:0;width:690px;top:1170px;text-align:center;font-size:6.6px;color:var(--white)}
</style>
</head>
<body>
<div class="abs hero" role="img" aria-label="Nature photo of orange canyon rock spires under a blue sky"></div>

<div class="abs brand"><span class="brand-mark"></span><span class="brand-name">Sam Verhoeven<span class="brand-sub">LIFECOACH</span></span></div>
<nav class="abs nav"><span class="active">Home</span><span>About us</span><span>Services</span><span>Gallery</span><span>Blog</span><span>Testimonials</span><span>Contact us</span></nav>
<div class="abs social-rail"><span></span><span></span><span></span><span></span></div>
<div class="abs dots"><span></span><span></span><span></span><span></span><span></span><span></span></div>

<div class="abs band"></div>
<div class="abs band-text">We specialize in transition life coaching for personal and professional empowerment</div>
<div class="abs band-btn">Learn More</div>

<h1 class="abs welcome-title">WELCOME SAM VERHOEVEN</h1>
<p class="abs welcome-text">Sed ut perspiciatis unde omnis iste natus error sit voluptatem accusantium doloremque laudantium, totam rem aperiam, eaqum aperiam, eaque ipsa e ipsa quae ab e veritatis et quasi architecto beatae vitae dicta sunt explicabo. Nemo enim ipsam voluptatem quia voluptas sit aspernatur aut odit aut fugm aperiam, eaque ipsa sequuntur magni dolores eos qui ratione voluptatem sequi nesciunt. Neque porro quisquam est, qui dolorem ipsum quia dolor sit amem aperiam, eaque ipsa t isci velit, sed quia non numquam eius modi tempora incidunt ut labore et dolore magnam aliquam quaerat voluptatem. Ut enim ad mim aperiam, eaque a n ostrum exercitm aperiam, eaque ipsa m aperiam, eaque ipsa m aperiam, eaque ipsa ationem ullam corporis suscipit laboriosam.</p>

<article class="abs card" style="left:75px">
  <div class="card-photo" role="img" aria-label="Two people jumping joyfully on green grass under a blue sky" style="background:linear-gradient(180deg,#2f6fd0 0%,#8db8ec 70%,#6cb33a 86%,#4e9a2c 100%)"></div>
  <h3>Life Coaching for Personal</h3>
  <p>Lorem ipsum dolor sit amet, consectetur adipisicing elit ed do eiusmod tempor incididunt ut labore et dolore m na aliqua. Ut enim ad minim veniam, quis nostrud exer ation ullamco laboris nisi.</p>
  <span class="pill">Read More</span>
</article>
<article class="abs card" style="left:262px">
  <div class="card-photo" role="img" aria-label="Man with raised arms on a meadow facing a bright sunrise" style="background:linear-gradient(180deg,#3e5f7c 0%,#c9c9a8 45%,#f4f0c8 60%,#7fb13a 80%,#4b8a22 100%)"></div>
  <h3>Life Coaching for&nbsp; Professional</h3>
  <p>Lorem ipsum dolor sit amet, consectetur adipisicing elit ed do eiusmod tempor incididunt ut labore et dolore m na aliqua. Ut enim ad minim veniam, quis nostrud exer ation ullamco laboris nisi.</p>
  <span class="pill">Read More</span>
</article>
<article class="abs card" style="left:449px">
  <div class="card-photo" role="img" aria-label="Woman in yellow with open arms in a sunny field" style="background:linear-gradient(180deg,#6fa6d6 0%,#b9d3e8 55%,#d7c36a 85%,#b5a63c 100%)"></div>
  <h3>Sam Verhoeven Other Services</h3>
  <p>Lorem ipsum dolor sit amet, consectetur adipisicing elit ed do eiusmod tempor incididunt ut labore et dolore m na aliqua. Ut enim ad minim veniam, quis nostrud exer ation ullamco laboris nisi.</p>
  <span class="pill">Read More</span>
</article>

<section class="abs testimonials"></section>
<h2 class="abs testi-title">CLIENT TESTMINOLAS</h2>
<div class="abs testi-rule"></div>
<blockquote class="abs quote" style="left:75px"><span class="quote-mark">&ldquo;</span><p>Llorejjamet, concvhcgdsectetur adipisicij ed do eiusmod tempor incididunt ut labore et dol na aliqua. Ut enim ad minim veniam, quis nostrud ed do eiusmod tempor incididunt ut labore et dol na aliqua. Ut enim ad minim veniam, quis nostru ation ullamco laboris nisi.</p><div class="who">Name , City Name</div></blockquote>
<blockquote class="abs quote" style="left:270px"><span class="quote-mark">&ldquo;</span><p>Llorejjamet, concvhcgdsectetur adipisicij ed do eiusmod tempor incididunt ut labore et dol na aliqua. Ut enim ad minim veniam, quis nostrud ed do eiusmod tempor incididunt ut labore et dol na aliqua. Ut enim ad minim veniam, quis nostru ation ullamco laboris nisi.</p><div class="who">Name , City Name</div></blockquote>
<blockquote class="abs quote" style="left:465px"><span class="quote-mark">&ldquo;</span><p>Llorejjamet, concvhcgdsectetur adipisicij ed do eiusmod tempor incididunt ut labore et dol na aliqua. Ut enim ad minim veniam, quis nostrud ed do eiusmod tempor incididunt ut labore et dol na aliqua. Ut enim ad minim veniam, quis nostru ation ullamco laboris nisi.</p><div class="who">Name , City Name</div></blockquote>

<footer class="abs footer"></footer>
<h4 class="abs foot-h" style="left:75px">Other Information</h4>
<ul class="abs foot-links" style="left:75px"><li>At vero eos</li><li>Odio dignissmos</li><li>Praesentum voluptum deleniti</li><li>Odio dignissmos duci</li><li>Praesentum voluptum</li><li>Praesentum voluptum</li></ul>
<ul class="abs foot-links" style="left:202px"><li>At vero eos</li><li>Odio dignissmos</li><li>Praesentum volui</li><li>Odio dignissmo</li><li>Praesentum vo</li><li>Praesentum vol</li></ul>
<h4 class="abs foot-h" style="left:302px">Customer Chirper</h4>
<div class="abs tweet"><span style="font-size:11px;font-weight:700">&ldquo;</span><br>At vero eos et accusamfhgzhzfuset io ssimosducimus qui.Azxgcfhgt vero eo et iusto odio dignissi...................... <b style="font-size:11px">&rdquo;</b><div class="date">Feb 24-104</div></div>
<div class="abs tweet-btn">Follow us Chirper</div>
<h4 class="abs foot-h" style="left:475px">Newsletter</h4>
<div class="abs mail">Mail</div>
<div class="abs submit">SUBMIT</div>
<div class="abs follow">Follow Us<span></span><span></span><span></span><span></span></div>
<div class="abs foot-rule"></div>
<p class="abs legal">&copy;2014 all copyrights are reserved &nbsp;| Terms and Conditions I Privacy Policy I Company Information</p>
</body>
</html>
```